Web Developer Needs a Business Card Design

I need a personal business card design that represents me as a web developer for potential employers. I would like the background to be a dark color on the front for contrast with my logo and name. The back will have all my information along with a smaller version of the logo. I want something with a modern look and feel, not too conservative. This will be used for potential employers and freelance work.

Industry/Entity Type

Business

Contact Information for Business Card

Front should have my logo and name. The back should have all my personal information which would include: name: Tom Varulek, phone: 570-614-3098, email: tomvarulek@quillbox.net, website url: www.tomvarulek.net, logo, web developer.

Font styles to use
Sans Serif

Requirements
Must have
• Must include my logo. The color palette base color will be the logo color.

```html
<!DOCTYPE html>
<html lang="en">
<head>
<meta charset="utf-8">
<title>Tom Varulek — Business Card</title>
<link rel="stylesheet" href="https://fonts.googleapis.com/css2?family=Lato:wght@400;700&display=swap">
<style>
  :root {
    --brand-green: #248b73;
    --ink: #1e1e1e;
    --paper: #ffffff;
    --backdrop: #1b1b1b;
    --band-dark: #000000;
  }
  * { margin: 0; padding: 0; box-sizing: border-box; }
  html, body {
    width: 1200px; height: 1086px; overflow: hidden;
    background: var(--backdrop);
    font-family: "Lato", sans-serif;
  }
  .card {
    position: absolute; left: 254px; width: 678px; height: 386px;
    border-radius: 8px; overflow: hidden;
  }
  .card--front { top: 126px; background: var(--paper); }
  .card--back { top: 586px; background: var(--brand-green); color: var(--paper); }

  .brand-mark {
    position: absolute; left: 138px; top: 118px;
    width: 116px; height: 116px; border-radius: 50%;
    border: 9px solid var(--brand-green);
  }
  .brand-name {
    position: absolute; left: 46px; width: 300px; top: 244px;
    text-align: center; font-weight: 700; font-size: 29px;
    color: var(--brand-green); letter-spacing: 0.2px;
  }
  .divider {
    position: absolute; left: 338px; top: 128px; width: 2px; height: 131px;
    background: linear-gradient(var(--brand-green) 0 33%, var(--ink) 33% 100%);
  }
  .person { position: absolute; left: 366px; top: 124px; }
  .person__name { font-weight: 700; font-size: 27px; color: var(--brand-green); line-height: 1.1; }
  .person__role { font-size: 21px; color: var(--ink); line-height: 1.3; }
  .contact { position: absolute; left: 366px; top: 210px; font-size: 22px; color: var(--ink); }
  .contact__row { display: flex; align-items: center; gap: 8px; height: 27px; }
  .contact__row svg { width: 20px; height: 18px; fill: var(--brand-green); flex: none; }
  .band { position: absolute; left: 0; right: 0; bottom: 0; height: 23px; display: flex; }
  .band__accent { width: 454px; background: var(--brand-green); }
  .band__url {
    flex: 1; background: var(--band-dark); color: var(--paper);
    font-size: 16px; line-height: 23px; padding-left: 22px;
  }

  .back-mark {
    position: absolute; left: 68px; top: 76px; width: 240px; height: 240px;
    border-radius: 50%; border: 18px solid var(--paper);
    display: flex; align-items: center; justify-content: center;
  }
  .back-mark__name { font-weight: 700; font-size: 24px; color: var(--paper); }
  .specialties { position: absolute; left: 384px; top: 56px; }
  .specialties__title { font-weight: 700; font-size: 22px; margin-bottom: 6px; }
  .specialties__list { list-style: none; font-size: 19px; }
  .specialties__list li { display: flex; align-items: center; gap: 7px; height: 21.7px; }
  .specialties__list svg { width: 16px; height: 14px; flex: none; }
</style>
</head>
<body>
  <section class="card card--front">
    <div class="brand-mark"></div>
    <div class="brand-name">TOM VARULEK</div>
    <div class="divider"></div>
    <div class="person">
      <div class="person__name">Tom Varulek</div>
      <div class="person__role">President</div>
    </div>
    <div class="contact">
      <div class="contact__row">
        <svg viewBox="0 0 20 18"><path d="M1 6c0-3 4-4 9-4s9 1 9 4v2h-4V6c-2-1-8-1-10 0v2H1z"/><path d="M5 9h10l2 8H3z"/></svg>
        <span>570-614-3098</span>
      </div>
      <div class="contact__row">
        <svg viewBox="0 0 20 18"><path d="M1 3h18v13H1zM3 5v9h14V5l-7 6z"/></svg>
        <span>tomvarulek@quillbox.net</span>
      </div>
    </div>
    <div class="band">
      <div class="band__accent"></div>
      <div class="band__url">www.tomvarulek.net</div>
    </div>
  </section>

  <section class="card card--back">
    <div class="back-mark"><span class="back-mark__name">TOM VARULEK</span></div>
    <div class="specialties">
      <div class="specialties__title">We Specialize In:</div>
      <ul class="specialties__list">
        <li><svg viewBox="0 0 16 14"><path d="M1 2h10v2H3v8h8V8h2v6H1z" fill="#fff"/><path d="M4 7l2-2 2 3 6-8 1 2-7 9z" fill="#fff"/></svg>HTML5/CSS3</li>
        <li><svg viewBox="0 0 16 14"><path d="M1 2h10v2H3v8h8V8h2v6H1z" fill="#fff"/><path d="M4 7l2-2 2 3 6-8 1 2-7 9z" fill="#fff"/></svg>Javascript</li>
        <li><svg viewBox="0 0 16 14"><path d="M1 2h10v2H3v8h8V8h2v6H1z" fill="#fff"/><path d="M4 7l2-2 2 3 6-8 1 2-7 9z" fill="#fff"/></svg>DOM Scripting</li>
        <li><svg viewBox="0 0 16 14"><path d="M1 2h10v2H3v8h8V8h2v6H1z" fill="#fff"/><path d="M4 7l2-2 2 3 6-8 1 2-7 9z" fill="#fff"/></svg>AJAX</li>
        <li><svg viewBox="0 0 16 14"><path d="M1 2h10v2H3v8h8V8h2v6H1z" fill="#fff"/><path d="M4 7l2-2 2 3 6-8 1 2-7 9z" fill="#fff"/></svg>SPA Frameworks</li>
        <li><svg viewBox="0 0 16 14"><path d="M1 2h10v2H3v8h8V8h2v6H1z" fill="#fff"/><path d="M4 7l2-2 2 3 6-8 1 2-7 9z" fill="#fff"/></svg>Version Control</li>
        <li><svg viewBox="0 0 16 14"><path d="M1 2h10v2H3v8h8V8h2v6H1z" fill="#fff"/><path d="M4 7l2-2 2 3 6-8 1 2-7 9z" fill="#fff"/></svg>Build Tools</li>
        <li><svg viewBox="0 0 16 14"><path d="M1 2h10v2H3v8h8V8h2v6H1z" fill="#fff"/><path d="M4 7l2-2 2 3 6-8 1 2-7 9z" fill="#fff"/></svg>CSS Preprocessing</li>
        <li><svg viewBox="0 0 16 14"><path d="M1 2h10v2H3v8h8V8h2v6H1z" fill="#fff"/><path d="M4 7l2-2 2 3 6-8 1 2-7 9z" fill="#fff"/></svg>Web Performance</li>
        <li><svg viewBox="0 0 16 14"><path d="M1 2h10v2H3v8h8V8h2v6H1z" fill="#fff"/><path d="M4 7l2-2 2 3 6-8 1 2-7 9z" fill="#fff"/></svg>Responsive Design</li>
        <li><svg viewBox="0 0 16 14"><path d="M1 2h10v2H3v8h8V8h2v6H1z" fill="#fff"/><path d="M4 7l2-2 2 3 6-8 1 2-7 9z" fill="#fff"/></svg>UX/UI Design</li>
      </ul>
    </div>
  </section>
</body>
</html>
```